Business Card Design for Marketing Firm

Looking for business card design for higher end marketing firm. Clean but impressionable/trendy. We are a marketing firm that represents manufacturers in the foodservice equipment and supply industry. Our customers are end users such has hotels, restaurants, country clubs, convention centers and casinos as well as distributors of restaurants supplies and equipment, and manufacturers of foodservice equipment and supplies.
Target Market(s)
Hotels, Restaurants, Supply & Equipment Distributors, Foodservice Manufacturers
Industry/Entity Type
Foodservice/Hospitality
Contact Information for Business Card
Name, Title, Contact Number, Email, Website, Social Media, Address
Requirements
Must have
- Clean & Simple but Serious and Impressionable

```html
<!DOCTYPE html>
<html lang="en">
<head>
<meta charset="UTF-8">
<title>Harbor Table Reps – Business Card</title>
<link href="https://fonts.googleapis.com/css2?family=Montserrat:wght@400;500;600&display=swap" rel="stylesheet">
<style>
  :root {
    --backdrop: #d8d2c8;
    --card-white: #ffffff;
    --navy: #2f3573;
    --navy-text: #2a2f68;
    --ink-soft: #4a4d66;
    --rule: #2f3573;
  }
  * { box-sizing: border-box; margin: 0; padding: 0; }
  html, body { width: 900px; height: 1200px; overflow: hidden; }
  body {
    background: var(--backdrop);
    font-family: "Montserrat", sans-serif;
    position: relative;
  }
  .card {
    position: absolute;
    left: 80px;
    width: 740px;
    height: 440px;
    border-radius: 34px;
    box-shadow: 0 10px 24px rgba(0,0,0,0.22);
  }
  .card-front { top: 125px; background: var(--card-white); }
  .card-back { top: 640px; background: var(--navy); display: flex; align-items: center; justify-content: center; }

  .contact-block {
    position: absolute;
    top: 170px;
    left: 0; right: 0;
    display: flex;
    justify-content: center;
    align-items: center;
  }
  .identity { text-align: right; padding-right: 22px; }
  .person-name {
    font-weight: 600;
    font-size: 25px;
    color: var(--navy-text);
    letter-spacing: 0.3px;
  }
  .person-title {
    font-size: 12px;
    color: var(--ink-soft);
    margin-top: 4px;
  }
  .divider { width: 2px; height: 78px; background: var(--rule); }
  .contact-list { list-style: none; padding-left: 18px; }
  .contact-item {
    display: flex; align-items: center;
    font-size: 12.5px; color: var(--ink-soft);
    line-height: 25px;
  }
  .contact-icon { width: 15px; height: 15px; margin-right: 9px; flex: none; }
  .address {
    position: absolute;
    bottom: 70px; left: 0; right: 0;
    text-align: center;
    font-size: 13px;
    color: var(--ink-soft);
  }
  .brand-lockup { display: flex; align-items: center; gap: 18px; }
  .brand-dot { width: 14px; height: 14px; border-radius: 50%; background: #ffffff; }
  .brand-name {
    font-family: "Montserrat", sans-serif;
    font-weight: 500;
    font-size: 38px;
    letter-spacing: 3px;
    color: #ffffff;
  }
</style>
</head>
<body>
  <section class="card card-front" aria-label="Business card front">
    <div class="contact-block">
      <div class="identity">
        <p class="person-name">Daniel Reyes</p>
        <p class="person-title">CEO &amp; Founder</p>
      </div>
      <div class="divider"></div>
      <ul class="contact-list">
        <li class="contact-item">
          <svg class="contact-icon" viewBox="0 0 16 16"><circle cx="8" cy="8" r="8" fill="#2f3573"/><path d="M5.3 4.2l1.3 0 .6 1.7-.8.6a5 5 0 0 0 2.3 2.3l.6-.8 1.7.6v1.3c0 .4-.4.8-.8.7A6.3 6.3 0 0 1 4.6 5c0-.4.3-.8.7-.8z" fill="#fff"/></svg>
          (555) 014-2280
        </li>
        <li class="contact-item">
          <svg class="contact-icon" viewBox="0 0 16 16"><circle cx="8" cy="8" r="8" fill="#2f3573"/><rect x="4" y="5.2" width="8" height="5.6" rx="0.6" fill="#fff"/><path d="M4.3 5.5L8 8.4l3.7-2.9" stroke="#2f3573" stroke-width="0.9" fill="none"/></svg>
          info@harbortablereps.com
        </li>
        <li class="contact-item">
          <svg class="contact-icon" viewBox="0 0 16 16"><circle cx="8" cy="8" r="8" fill="#2f3573"/><circle cx="8" cy="8" r="3.8" stroke="#fff" stroke-width="0.9" fill="none"/><ellipse cx="8" cy="8" rx="1.6" ry="3.8" stroke="#fff" stroke-width="0.8" fill="none"/><path d="M4.2 8h7.6" stroke="#fff" stroke-width="0.8"/></svg>
          www.harbortablereps.com
        </li>
      </ul>
    </div>
    <p class="address">450 Market Lane, Suite 210, Bayview, CA 90210</p>
  </section>

  <section class="card card-back" aria-label="Business card back">
    <div class="brand-lockup">
      <span class="brand-dot"></span>
      <span class="brand-name">HARBOR TABLE REPS</span>
    </div>
  </section>
</body>
</html>
```